UI/ UX Design for ERP Software

We need a new UX/UI interface for a ERP software for property managers. Our CMMS / ERP solution is made based on responsive design technologies and is coded in PHP.
The overall UX to be similar to Tev Ulna - easy navigation, intuitive menus.

Industry/Entity Type

Property Management

Number of Pages Required

5+ page

Requirements
Must have
• Round dock buttons
Consistent icons across the application
Enough Spacing between buttons/icons/ menu
Consistent Font
Nice to have
• We would like the UX to allow the users to use the application without /minimum training.
Should not have
• we don't want anything that is classic with respect to UX

```html
<!DOCTYPE html>
<html lang="en">
<head>
<meta charset="utf-8">
<title>Nestwell – Active Dashboard</title>
<link rel="stylesheet" href="https://fonts.googleapis.com/css2?family=Roboto:wght@400;500&display=swap">
<style>
  :root{
    --page:#f5f5f6;
    --header:#f3f7fc;
    --line:#dfe5ec;
    --brand:#1ba6f0;
    --bar:#12aefc;
    --ink:#4a4f55;
    --muted:#5f656c;
    --grid:#e3e6ea;
    --green:#a6ce39;
    --orange:#f7941d;
    --purple:#5b2d8f;
    --pink:#e0176e;
    --footer:#4f6279;
  }
  *{box-sizing:border-box;margin:0;padding:0}
  html,body{width:1200px;height:874px;overflow:hidden}
  body{font-family:"Roboto",sans-serif;background:var(--page);color:var(--ink);position:relative}

  .topbar{position:absolute;left:0;top:0;width:1200px;height:82px;background:var(--header);border-bottom:1px solid var(--line)}
  .brand{position:absolute;left:0;top:0;width:231px;height:82px;border-right:1px solid var(--line);display:flex;align-items:center;gap:8px;padding-left:56px}
  .brand-mark{width:14px;height:14px;border-radius:50%;background:var(--brand)}
  .brand-name{font-size:26px;font-weight:500;color:var(--brand)}
  .page-title{position:absolute;left:249px;top:32px;display:flex;align-items:center;gap:9px;font-size:17.5px;color:var(--ink)}
  .stat{position:absolute;top:26px;text-align:center}
  .stat-label{font-size:10px;letter-spacing:.2px;color:var(--muted)}
  .stat-value{font-size:12.5px;margin-top:5px;display:flex;align-items:center;justify-content:center;gap:4px}
  .divider{position:absolute;top:24px;width:1px;height:39px;background:var(--line)}
  .menu-dock{position:absolute;left:1103px;top:22px;width:43px;height:43px;border-radius:50%;background:var(--bar);display:flex;align-items:center;justify-content:center}

  .panel{position:absolute;left:52px;top:120px;width:1094px;height:589px;background:#fff;border:1px solid #ececec}
  .range-bar{height:54px;background:var(--bar);position:relative}
  .range-btn{position:absolute;top:9px;height:35px;border:1px solid rgba(255,255,255,.85);color:#fff;font-size:12px;font-weight:500;display:flex;align-items:center;justify-content:center;gap:5px}
  .period{position:absolute;left:33px;top:86px;display:flex;align-items:flex-end;gap:10px;font-size:14px;color:var(--ink)}
  .chart{position:absolute;left:0;top:0}

  .footer{position:absolute;left:0;top:823px;width:1200px;height:51px;background:var(--footer);color:#fff;font-size:11px;display:flex;align-items:center;justify-content:center}
</style>
</head>
<body>

<header class="topbar">
  <div class="brand"><span class="brand-mark"></span><span class="brand-name">Nestwell</span></div>
  <div class="page-title">
    <svg width="18" height="15" viewBox="0 0 18 15"><path d="M9 0 0 7.5h2.5V15h4.5v-5h4v5h4.5V7.5H18z" fill="#4a4f55"/></svg>
    Active Dashboard
  </div>

  <div class="divider" style="left:466px"></div>
  <div class="stat" style="left:481px">
    <div class="stat-label">PROPERTIES</div>
    <div class="stat-value" style="color:var(--brand)"><svg width="12" height="10" viewBox="0 0 18 15"><path d="M9 0 0 7.5h2.5V15h4.5v-5h4v5h4.5V7.5H18z" fill="currentColor"/></svg>03</div>
  </div>
  <div class="divider" style="left:561px"></div>
  <div class="stat" style="left:578px">
    <div class="stat-label">TENANTS</div>
    <div class="stat-value" style="color:var(--green)"><svg width="15" height="11" viewBox="0 0 15 11"><circle cx="7.5" cy="3" r="2.5" fill="currentColor"/><circle cx="3" cy="3.5" r="2" fill="currentColor"/><circle cx="12" cy="3.5" r="2" fill="currentColor"/><path d="M3 11c0-3 2-5 4.5-5S12 8 12 11z M0 10c0-2 1.5-3.5 3-3.5L3 10z M15 10c0-2-1.5-3.5-3-3.5L12 10z" fill="currentColor"/></svg>08</div>
  </div>
  <div class="divider" style="left:644px"></div>
  <div class="stat" style="left:665px">
    <div class="stat-label">TOTAL PROPERTIES AREA</div>
    <div class="stat-value" style="color:var(--orange)"><svg width="13" height="11" viewBox="0 0 13 11"><rect x="5" y="0" width="3" height="3" fill="currentColor"/><path d="M6.5 3v2.5M2 8V5.5h9V8" stroke="currentColor" fill="none"/><rect x="0" y="8" width="3" height="3" fill="currentColor"/><rect x="5" y="8" width="3" height="3" fill="currentColor"/><rect x="10" y="8" width="3" height="3" fill="currentColor"/></svg>422,000.00 sq.ft</div>
  </div>
  <div class="divider" style="left:809px"></div>
  <div class="stat" style="left:824px">
    <div class="stat-label">RENTED AREA</div>
    <div class="stat-value" style="color:var(--purple)"><svg width="13" height="11" viewBox="0 0 13 11"><rect x="5" y="0" width="3" height="3" fill="currentColor"/><path d="M6.5 3v2.5M2 8V5.5h9V8" stroke="currentColor" fill="none"/><rect x="0" y="8" width="3" height="3" fill="currentColor"/><rect x="5" y="8" width="3" height="3" fill="currentColor"/><rect x="10" y="8" width="3" height="3" fill="currentColor"/></svg>233,500.00 sq.ft</div>
  </div>
  <div class="divider" style="left:948px"></div>
  <div class="stat" style="left:968px">
    <div class="stat-label">VACANCIES AREA</div>
    <div class="stat-value" style="color:var(--pink)"><svg width="13" height="11" viewBox="0 0 13 11"><rect x="5" y="0" width="3" height="3" fill="currentColor"/><path d="M6.5 3v2.5M2 8V5.5h9V8" stroke="currentColor" fill="none"/><rect x="0" y="8" width="3" height="3" fill="currentColor"/><rect x="5" y="8" width="3" height="3" fill="currentColor"/><rect x="10" y="8" width="3" height="3" fill="currentColor"/></svg>188,500.00sq.ft</div>
  </div>
  <div class="divider" style="left:1088px"></div>
  <div class="menu-dock">
    <svg width="12" height="10" viewBox="0 0 12 10"><path d="M0 1h12M0 5h12M0 9h12" stroke="#fff" stroke-width="1.8"/></svg>
  </div>
</header>

<section class="panel">
  <div class="range-bar">
    <div class="range-btn" style="left:416px;width:105px"><svg width="11" height="11" viewBox="0 0 12 12"><circle cx="6" cy="6" r="5" stroke="#fff" stroke-width="1.6" fill="none"/><path d="M6 3.2V6h2" stroke="#fff" stroke-width="1.4" fill="none"/></svg>Last 7 Days</div>
    <div class="range-btn" style="left:526px;width:105px"><svg width="11" height="11" viewBox="0 0 12 12"><circle cx="6" cy="6" r="5" stroke="#fff" stroke-width="1.6" fill="none"/><path d="M6 3.2V6h2" stroke="#fff" stroke-width="1.4" fill="none"/></svg>Last months</div>
    <div class="range-btn" style="left:636px;width:115px"><svg width="11" height="11" viewBox="0 0 12 12"><circle cx="6" cy="6" r="5" stroke="#fff" stroke-width="1.6" fill="none"/><path d="M6 3.2V6h2" stroke="#fff" stroke-width="1.4" fill="none"/></svg>Last 3 months</div>
    <div class="range-btn" style="left:757px;width:101px"><svg width="11" height="11" viewBox="0 0 12 12"><circle cx="6" cy="6" r="5" stroke="#fff" stroke-width="1.6" fill="none"/><path d="M6 3.2V6h2" stroke="#fff" stroke-width="1.4" fill="none"/></svg>Next 7 Days</div>
    <div class="range-btn" style="left:862px;width:101px"><svg width="11" height="11" viewBox="0 0 12 12"><circle cx="6" cy="6" r="5" stroke="#fff" stroke-width="1.6" fill="none"/><path d="M6 3.2V6h2" stroke="#fff" stroke-width="1.4" fill="none"/></svg>Next months</div>
    <div class="range-btn" style="left:968px;width:114px"><svg width="11" height="11" viewBox="0 0 12 12"><circle cx="6" cy="6" r="5" stroke="#fff" stroke-width="1.6" fill="none"/><path d="M6 3.2V6h2" stroke="#fff" stroke-width="1.4" fill="none"/></svg>Next 3 months</div>
  </div>

  <div class="period">
    <svg width="27" height="27" viewBox="0 0 27 27"><path d="M1 26V14h4v12M8 26V17h4v9M15 26V11h4v15" stroke="#1ba6f0" fill="none"/><path d="M21 26V1h4v25" stroke="#4a4f55" fill="none"/><path d="M0 26.5h27" stroke="#1ba6f0"/></svg>
    <span>12/27/2020 - 01/03/2021</span>
  </div>

  <svg class="chart" width="1094" height="589" viewBox="0 0 1094 589" font-family="Roboto, sans-serif">
    <g stroke="#666" stroke-width="1.6"><path d="M82 174h11M82 178h11M82 182h11"/></g>
    <g stroke="var(--grid)" stroke-width="1">
      <path d="M138 179H1051M138 234H1051M138 290H1051M138 345H1051M138 401H1051"/>
    </g>
    <path d="M138 456H1051" stroke="#c9ced4"/>
    <g stroke="#c9ced4"><path d="M138 456v8M252 456v8M366 456v8M480 456v8M594 456v8M708 456v8M822 456v8M937 456v8M1051 456v8"/></g>
    <g fill="var(--muted)" font-size="9.5" text-anchor="end">
      <text x="129" y="182">1.25</text><text x="129" y="238">1</text><text x="129" y="293">0.75</text>
      <text x="129" y="349">0.5</text><text x="129" y="404">0.25</text><text x="129" y="460">0</text>
    </g>
    <text transform="translate(61 322) rotate(-90)" text-anchor="middle" font-size="13" fill="var(--muted)">Number</text>
    <rect x="488" y="234" width="18" height="222" fill="var(--green)"/>
    <g fill="var(--muted)" font-size="9.5" text-anchor="middle">
      <text x="192" y="476">12/27/2020</text><text x="306" y="476">12/28/2020</text><text x="421" y="476">12/29/2020</text>
      <text x="535" y="476">12/30/2020</text><text x="649" y="476">12/31/2020</text><text x="763" y="476">01/01/2021</text>
      <text x="877" y="476">01/02/2021</text><text x="992" y="476">01/03/2021</text>
    </g>
    <g font-size="10.5" fill="var(--muted)">
      <rect x="138" y="518" width="16" height="14" fill="#4f6279"/><text x="161" y="528">Scheduled</text><text x="161" y="543">Maintenance</text>
      <rect x="271" y="518" width="16" height="14" fill="#f7941d"/><text x="295" y="528">Completed</text><text x="295" y="543">Scheduled</text><text x="295" y="559">Maintenance</text>
      <rect x="405" y="518" width="16" height="14" fill="#0a9c4a"/><text x="429" y="528">Future Scheduled</text><text x="429" y="543">Maintenance</text>
      <rect x="539" y="518" width="16" height="14" fill="#12aefc"/><text x="563" y="528">Scheduled Work</text><text x="563" y="543">Orders</text>
      <rect x="672" y="518" width="16" height="14" fill="#6a3293"/><text x="696" y="528">Completed work</text><text x="696" y="543">Orders</text>
      <rect x="806" y="518" width="16" height="14" fill="#e0178a"/><text x="830" y="528">Property Inspections</text><text x="830" y="543">in Progress</text>
      <rect x="940" y="518" width="16" height="14" fill="#ecd22c"/><text x="964" y="528">Completed Property</text><text x="964" y="543">Inspections</text>
    </g>
  </svg>
</section>

<footer class="footer">© Copyrights 2021- Nestwell. All Rights Reserved.</footer>

</body>
</html>
```